Fernhale Business Card Design

We are looking for a fresh business card design for our new logo. We would like a business card that is unique but friendly. We are in the window coverings business offering blinds, shutters and shades for homes.

Target Market(s)

Targeting the end-consumer

Industry/Entity Type

Business

Requirements
Must have
• Must have a dedicates space for a photo of our sales person. Must contain our new logo (attached).

```html
<!DOCTYPE html>
<html lang="en">
<head>
<meta charset="UTF-8">
<title>Fernhale Business Card</title>
<link rel="stylesheet" href="https://fonts.googleapis.com/css2?family=Marcellus&family=Roboto:wght@400;500&family=Roboto+Condensed:wght@700&display=swap">
<style>
  :root {
    --backdrop: #2b2b2d;
    --card-light: #f4f4f4;
    --card-dark: #2a2a2b;
    --ink-dark: #5a5a5a;
    --ink-light: #ffffff;
    --accent: #8dc63f;
    --muted: #8a8a8a;
    --photo-top: #9a9a9a;
    --photo-bottom: #8a8a8a;
  }
  * { margin: 0; padding: 0; box-sizing: border-box; }
  html, body { width: 1200px; height: 900px; overflow: hidden; }
  body {
    background: var(--backdrop);
    display: flex;
    flex-direction: column;
    align-items: center;
    justify-content: center;
    gap: 24px;
    font-family: "Roboto", Arial, sans-serif;
  }
  .card {
    position: relative;
    width: 700px;
    height: 390px;
    overflow: hidden;
    box-shadow: 0 12px 30px rgba(0,0,0,.45);
  }
  .card-front { background: var(--card-light); }
  .card-back { background: var(--card-dark); }

  /* front */
  .brand {
    position: absolute;
    left: 60px;
    top: 56px;
    display: flex;
    align-items: center;
    gap: 12px;
  }
  .brand-mark {
    width: 34px;
    height: 34px;
    background: var(--accent);
    border-radius: 4px;
  }
  .brand-name {
    font-family: "Marcellus", Georgia, serif;
    font-size: 40px;
    color: var(--ink-dark);
    line-height: 1;
  }
  .brand-url {
    position: absolute;
    left: 62px;
    top: 112px;
    font-family: "Marcellus", Georgia, serif;
    font-size: 14px;
    letter-spacing: 7px;
    color: var(--ink-dark);
  }
  .staff-photo {
    position: absolute;
    left: 400px;
    top: 70px;
    width: 270px;
    height: 320px;
    border-radius: 90px 90px 0 0;
    background: linear-gradient(180deg, var(--photo-top), var(--photo-bottom));
  }

  /* back */
  .identity {
    position: absolute;
    right: 380px;
    top: 98px;
    text-align: right;
  }
  .person-name {
    font-family: "Roboto Condensed", Arial, sans-serif;
    font-weight: 700;
    font-size: 38px;
    color: var(--accent);
    line-height: 1;
  }
  .person-role {
    font-size: 17px;
    color: var(--muted);
    margin-top: 4px;
    letter-spacing: .5px;
  }
  .divider {
    position: absolute;
    left: 345px;
    top: 82px;
    width: 2px;
    height: 130px;
    background: linear-gradient(180deg, transparent, #bdbdbd 30%, #bdbdbd 70%, transparent);
  }
  .contact-list {
    position: absolute;
    left: 370px;
    top: 86px;
    list-style: none;
  }
  .contact-item {
    display: flex;
    align-items: center;
    gap: 10px;
    height: 25px;
    font-size: 17px;
    font-weight: 500;
    color: var(--ink-light);
  }
  .icon { width: 16px; height: 16px; fill: var(--accent); flex: none; }
  .address {
    position: absolute;
    left: 60px;
    top: 290px;
    display: flex;
    align-items: center;
    gap: 6px;
    font-size: 19px;
    font-weight: 500;
    color: var(--ink-light);
  }
</style>
</head>
<body>

<section class="card card-front">
  <div class="brand">
    <span class="brand-mark"></span>
    <span class="brand-name">Fernhale</span>
  </div>
  <p class="brand-url">www.fernhale.com</p>
  <div class="staff-photo" role="img" aria-label="Photo of the sales person, shown from the chest up"></div>
</section>

<section class="card card-back">
  <div class="identity">
    <h1 class="person-name">DANIEL REYES</h1>
    <p class="person-role">CEO/FOUNDER</p>
  </div>
  <div class="divider"></div>
  <ul class="contact-list">
    <li class="contact-item">
      <svg class="icon" viewBox="0 0 16 16"><path d="M3.5 1l3 3-1.6 1.8c.8 1.9 2.4 3.5 4.3 4.3L11 8.5l3 3-1.8 2.5C7 14 2 9 2 3.8z"/></svg>
      512 308 4471
    </li>
    <li class="contact-item">
      <svg class="icon" viewBox="0 0 16 16"><path d="M4 1h8v14H4zM5.5 2.5v9h5v-9zM7 12.5h2v1H7z" fill-rule="evenodd"/></svg>
      741 205 6183
    </li>
    <li class="contact-item">
      <svg class="icon" viewBox="0 0 16 16"><path d="M4 1h8v4H4zM1 6h14v7h-3v2H4v-2H1zM5 10v4h6v-4z" fill-rule="evenodd"/></svg>
      390 772 5816
    </li>
    <li class="contact-item">
      <svg class="icon" viewBox="0 0 16 16"><path d="M1 3h14v10H1zM2 4.2v.5l6 4.3 6-4.3v-.5z" fill-rule="evenodd"/></svg>
      name@fernhale.com
    </li>
    <li class="contact-item">
      <svg class="icon" viewBox="0 0 16 16"><circle cx="8" cy="8" r="7"/><path d="M1 8h14M8 1c-3 3.5-3 10.5 0 14M8 1c3 3.5 3 10.5 0 14" stroke="#2a2a2b" stroke-width="1.2" fill="none"/></svg>
      www.fernhale.com
    </li>
  </ul>
  <p class="address">
    <svg class="icon" viewBox="0 0 16 16"><path d="M8 1a5 5 0 015 5c0 3.5-5 9-5 9S3 9.5 3 6a5 5 0 015-5zm0 3a2 2 0 100 4 2 2 0 000-4z" fill-rule="evenodd"/></svg>
    2140 Larchmont Road, Juneau, Alaska 34518
  </p>
</section>

</body>
</html>
```